Business Card Design For Office Furniture Clearance Company

Kestrel Office Clearance - our company name pretty much explains what we do, we clear offices for high end clients, mainly plc's and large international companies.

We require a nice looking business card that displays professionalism but without being too serious.

It would be nice to see just a little more than a conventional boring business card, make sure you add some flare.

Industry/Entity Type

Office Furniture

Contact Information for Business Card

CARD 1

Mark Holloway
Director
mark@kestrelofficeclearance.co.uk
m: 07700 153928

t: 01632 960418
www.kestrelofficeclearance.co.uk

Kestrel Office Clearance
Unit K4 B
2-8 Fenwick Lane
Bletchley
Milton Keynes
ZZ9 4QT

free office clearances… you cant get better than that.

CARD 2

Peter Radford
Director
peter@kestrelofficeclearance.co.uk
m: 07700 382615

t: 01632 960418

Kestrel Office Clearance
Unit K4 B
2-8 Fenwick Lane
Bletchley
Milton Keynes
ZZ9 4QT

Font styles to use
Sans Serif

Requirements
Must have
• A white background - as we have a blue logo.
Nice to have
• Nice use of the logo - play around with this and dissect it.

```html
<!DOCTYPE html>
<html lang="en">
<head>
<meta charset="utf-8">
<title>Kestrel Office Clearance – Business Card</title>
<link rel="stylesheet" href="https://fonts.googleapis.com/css2?family=Lato:wght@400;700;900&display=swap">
<style>
  :root {
    --brand-blue: #0a78be;
    --ink: #2b2b2b;
    --card-white: #ffffff;
    --backdrop: #e7e5e2;
  }
  * { box-sizing: border-box; margin: 0; padding: 0; }
  html, body {
    width: 1200px; height: 966px; overflow: hidden;
    background: var(--backdrop);
    font-family: "Lato", Arial, sans-serif;
  }
  .stage { position: relative; width: 1200px; height: 966px; }
  .card {
    position: absolute;
    width: 540px; height: 308px;
    border-radius: 12px;
    overflow: hidden;
    box-shadow: 0 2px 8px rgba(0,0,0,0.18);
  }
  .card--front { left: 47px; top: 291px; background: var(--card-white); }
  .card--back { left: 609px; top: 293px; background: var(--brand-blue); }

  .card__accent { position: absolute; inset: 0; }

  .front__company {
    position: absolute; left: 25px; top: 26px;
    color: var(--brand-blue); font-weight: 700; font-size: 26px; letter-spacing: -0.2px;
  }
  .front__name {
    position: absolute; left: 25px; top: 106px;
    color: var(--brand-blue); font-weight: 400; font-size: 21px;
  }
  .front__role {
    position: absolute; left: 25px; top: 131px;
    color: var(--ink); font-size: 12.5px;
  }
  .front__address {
    position: absolute; left: 25px; top: 169px;
    color: var(--ink); font-size: 12.5px; line-height: 15.6px;
    font-style: normal;
  }
  .front__contacts {
    position: absolute; left: 25px; top: 224px;
    list-style: none; color: var(--ink); font-size: 12.5px;
  }
  .front__contacts li { display: flex; align-items: center; height: 17.5px; }
  .front__contacts svg { width: 13px; height: 13px; margin-right: 6px; flex: none; }

  .back__brand {
    position: absolute; right: 37px; top: 224px;
    text-align: right; color: var(--card-white);
  }
  .back__company { font-weight: 700; font-size: 32px; line-height: 1; letter-spacing: -0.3px; }
  .back__web { margin-top: 4px; font-size: 10.5px; letter-spacing: 5.6px; margin-right: -5.6px; }
</style>
</head>
<body>
<main class="stage">

  <section class="card card--front" aria-label="Business card front">
    <svg class="card__accent" viewBox="0 0 540 308" aria-hidden="true">
      <circle cx="534" cy="154" r="154" fill="var(--brand-blue)"/>
    </svg>
    <h1 class="front__company">Kestrel Office Clearance</h1>
    <p class="front__name">Mark Holloway</p>
    <p class="front__role">Director</p>
    <address class="front__address">
      Unit K4 B, 2-8 Fenwick Lane<br>
      Ashcombe, Northbridge<br>
      ZZ9 4QT
    </address>
    <ul class="front__contacts">
      <li>
        <svg viewBox="0 0 16 16" aria-hidden="true"><rect x="4" y="1" width="8" height="14" rx="1.5" fill="none" stroke="var(--brand-blue)" stroke-width="1.6"/><line x1="7" y1="12.5" x2="9" y2="12.5" stroke="var(--brand-blue)" stroke-width="1.4"/></svg>
        07700 153928
      </li>
      <li>
        <svg viewBox="0 0 16 16" aria-hidden="true"><path d="M3.5 1.5l2.5 0 1 3.5-1.8 1.3c.9 2 2.3 3.4 4.3 4.3l1.3-1.8 3.5 1v2.5c0 1-1 1.7-2 1.6C6.5 13.4 2.6 9.5 2 3.5c-.1-1 .6-2 1.5-2z" fill="var(--brand-blue)"/></svg>
        01632 960418
      </li>
      <li>
        <svg viewBox="0 0 16 16" aria-hidden="true"><rect x="1" y="3" width="14" height="10" fill="var(--brand-blue)"/><path d="M1.5 3.5L8 9l6.5-5.5M1.5 12.5l5-4.5M14.5 12.5l-5-4.5" fill="none" stroke="#fff" stroke-width="1"/></svg>
        mark@kestrelofficeclearance.co.uk
      </li>
      <li>
        <svg viewBox="0 0 16 16" aria-hidden="true"><g fill="none" stroke="var(--brand-blue)" stroke-width="1.2"><circle cx="8" cy="8" r="6.5"/><ellipse cx="8" cy="8" rx="3" ry="6.5"/><line x1="1.5" y1="8" x2="14.5" y2="8"/><path d="M2.8 4.5h10.4M2.8 11.5h10.4"/></g></svg>
        www.kestrelofficeclearance.co.uk
      </li>
    </ul>
  </section>

  <section class="card card--back" aria-label="Business card back">
    <svg class="card__accent" viewBox="0 0 540 308" aria-hidden="true">
      <circle cx="7" cy="154" r="156" fill="none" stroke="var(--card-white)" stroke-width="3"/>
    </svg>
    <div class="back__brand">
      <p class="back__company">Kestrel Office Clearance</p>
      <p class="back__web">www.kestrelofficeclearance.co.uk</p>
    </div>
  </section>

</main>
</body>
</html>
```